Harbor Crestline (Business Card Design)

Need business cards designed. Something modern, chic, and sleek. Mabye the back of the card should be the navy blue that is in the logo and then just the logo on the back.

Target Market(s)

Those in the hotel, office, and renovation industry

Contact Information for Business Card

1. Logo 2. Dorian Fenwick 3. CEO/Founder 4. Phone: (833) HarbCre / (833) 427-2731 5. Email: dorian@theharborcrestline.com 6. Website: www.theharborcrestline.com

Font styles to use
Other font styles liked:
• Look at the logo font and base the font for everything else off of that.

Colors
0054AA
0677BA
7BADD7
CADEEF
E8F1F8

Requirements
Must have
• Colors that are associated in the logo
Nice to have
• Sleek modern clean and chic design.

```html
<!DOCTYPE html>
<html lang="en">
<head>
<meta charset="utf-8">
<title>Harbor Crestline — Business Card</title>
<link href="https://fonts.googleapis.com/css2?family=Montserrat:wght@300;400;500;600&display=swap" rel="stylesheet">
<style>
  :root {
    --backdrop: #dcdcdc;
    --paper: #f6f6f5;
    --navy: #23224a;
    --gold: #d5ab4a;
    --ink-light: #f2f2f0;
  }
  * { box-sizing: border-box; margin: 0; padding: 0; }
  html, body {
    width: 1200px;
    height: 900px;
    overflow: hidden;
  }
  body {
    background: var(--backdrop);
    font-family: "Montserrat", sans-serif;
    display: flex;
    flex-direction: column;
    align-items: center;
    justify-content: center;
    gap: 44px;
  }
  .card {
    position: relative;
    width: 620px;
    height: 354px;
    border-radius: 26px;
    box-shadow: 0 10px 28px rgba(0, 0, 0, 0.14);
    overflow: hidden;
  }

  /* Front */
  .card--front {
    background: var(--paper);
    display: flex;
    align-items: center;
    justify-content: center;
  }
  .wordmark {
    display: flex;
    align-items: center;
    gap: 16px;
  }
  .wordmark__name {
    color: var(--navy);
    font-weight: 500;
    font-size: 30px;
    letter-spacing: 0.22em;
    text-transform: uppercase;
  }
  .wordmark__mark {
    width: 12px;
    height: 12px;
    background: var(--gold);
  }

  /* Back */
  .card--back {
    background: var(--navy);
    color: var(--ink-light);
  }
  .card__accent {
    position: absolute;
    top: 64px;
    right: 64px;
    width: 24px;
    height: 24px;
    background: var(--gold);
  }
  .contact {
    position: absolute;
    left: 56px;
    bottom: 48px;
  }
  .contact__name {
    color: var(--gold);
    font-weight: 300;
    font-size: 26px;
    letter-spacing: 0.01em;
  }
  .contact__role {
    font-weight: 400;
    font-size: 15px;
    margin-top: 4px;
  }
  .contact__list {
    list-style: none;
    margin-top: 26px;
    display: flex;
    flex-direction: column;
    gap: 10px;
  }
  .contact__item {
    display: flex;
    align-items: center;
    gap: 14px;
    font-size: 15px;
    font-weight: 300;
  }
  .contact__item strong { font-weight: 600; }
  .contact__icon {
    width: 20px;
    height: 20px;
    flex: none;
  }
</style>
</head>
<body>

  <section class="card card--front" aria-label="Card front">
    <div class="wordmark">
      <span class="wordmark__name">Harbor Crestline</span>
      <span class="wordmark__mark" aria-hidden="true"></span>
    </div>
  </section>

  <section class="card card--back" aria-label="Card back">
    <span class="card__accent" aria-hidden="true"></span>
    <div class="contact">
      <p class="contact__name">Dorian Fenwick</p>
      <p class="contact__role">CEO/Founder</p>
      <ul class="contact__list">
        <li class="contact__item">
          <svg class="contact__icon" viewBox="0 0 20 20" aria-hidden="true">
            <rect x="2" y="4.5" width="16" height="11" rx="1" fill="none" stroke="var(--gold)" stroke-width="1.6"/>
            <path d="M2.5 5.5 L10 11 L17.5 5.5" fill="none" stroke="var(--gold)" stroke-width="1.6"/>
          </svg>
          <span>dorian@<strong>theharborcrestline.com</strong></span>
        </li>
        <li class="contact__item">
          <svg class="contact__icon" viewBox="0 0 20 20" aria-hidden="true">
            <path d="M5.5 2.5 l3 3 -1.8 2 c1 2.3 2.6 3.9 4.8 4.8 l2-1.8 3 3 -2 2.3 C8.7 16 4 11.3 3.2 4.5 Z" fill="var(--gold)"/>
          </svg>
          <span>(833) HarbCre / (833) 427-2731</span>
        </li>
      </ul>
    </div>
  </section>

</body>
</html>
```